1" x 3" label needed for essential oil bottle(s) - new ecommerce company

We need a label designed for 10 ml bottles of essential oils. We are offering 9 different types of essential oil: Lavender, Cedarwood, Eucalyptus, Frankincense, Lemon, Orange, Peppermint, Rosemary, and Tea Tree. The label should have a space for the type of essential oil. The bottles are an amber color (am including a photo) as essential oils are sensitive to light. also am including an AI file of our logo, which we'd like included on the label; the logo file also contains our logo colors, a dark blue and light grey. We'd also like the following on the label: "CAUTION: EYE AND SKIN IRRITANT. Avoid contact with eyes and skin. Wash hands after handling. If eye contact occurs, flush with water for 15 minutes. Not intended for topical or internal use. Contains Essential Oils. KEEP OUT OF REACH OF CHILDREN."
Also "Ingredients: 100% pure essential oil, GC tested."
Also "0.33 fl oz (10 ml)
Finally, we will need to include a sideways bar code on the right side of the label, so need 3/8" of white space on the right of the label.
We'd like the label to be calming, but modern, friendly, and confident.

```html
<!DOCTYPE html>
<html lang="en">
<head>
<meta charset="utf-8">
<title>Essential Oil Label Series</title>
<link href="https://fonts.googleapis.com/css2?family=Jost:wght@400;500&display=swap" rel="stylesheet">
<style>
  :root {
    --ink: #3d4856;
    --paper: #f4f1f0;
    --white: #ffffff;
    --lavender: #bab0cc;
    --cedarwood: #d3d7ea;
    --eucalyptus: #a2d6d6;
    --frankincense: #dea9a8;
    --lemon: #f5e3a8;
    --orange: #f9cba0;
    --peppermint: #a8c8b2;
    --rosemary: #ebc2cf;
    --teatree: #7a9a8a;
  }
  * { box-sizing: border-box; margin: 0; padding: 0; }
  html, body { width: 1200px; height: 991px; overflow: hidden; background: var(--white); }
  body { position: relative; font-family: "Jost", sans-serif; color: var(--ink); }

  .label {
    position: absolute;
    width: 56.6em; height: 23.8em;
    border-radius: 1.6em;
    background: var(--white);
    box-shadow: 0 0 0 0.06em #ece9e8;
    overflow: hidden;
  }
  .label__field {
    position: absolute; left: 0; top: 0;
    width: 84.2%; height: 100%;
  }
  .label__field svg { position: absolute; inset: 0; width: 100%; height: 100%; }
  .label__oil {
    position: absolute; left: 17.6%; top: 30%;
    transform: translate(-50%, -50%) rotate(-90deg);
    font-size: 1.74em; letter-spacing: 0.06em; white-space: nowrap; font-weight: 400;
  }
  .label__brand {
    position: absolute; left: 17.6%; top: 73%;
    transform: translateX(-50%);
    display: flex; flex-direction: column; align-items: center; gap: 0.55em;
  }
  .label__brand-dot {
    width: 1.5em; height: 1.5em; border-radius: 50%;
    border: 0.08em solid var(--ink);
  }
  .label__brand-name { font-size: 1.3em; letter-spacing: 0.32em; margin-right: -0.32em; }
  .label__caution {
    position: absolute; left: 57.5%; top: 16.5%;
    transform: translateX(-50%);
    text-align: center; line-height: 1.42em; white-space: nowrap;
  }
  .label__facts {
    position: absolute; left: 57.5%; top: 77.5%;
    transform: translateX(-50%);
    text-align: center; line-height: 1.42em; white-space: nowrap;
  }

  .label--frankincense { left: 407px; top: 72px; font-size: 12.5px; }
  .label--eucalyptus { left: 46px; top: 380px; font-size: 3.9px; }
  .label--lavender { left: 359px; top: 523px; font-size: 5.05px; }
  .label--peppermint { left: 657px; top: 523px; font-size: 5.05px; }
  .label--lemon { left: 359px; top: 781px; font-size: 5.05px; }
  .label--orange { left: 657px; top: 781px; font-size: 5.05px; }

  .palette {
    position: absolute; left: 983px; top: 520px;
    list-style: none;
  }
  .palette__item {
    display: flex; align-items: center; height: 28.3px;
    font-size: 19.5px; letter-spacing: 0.02em;
  }
  .palette__swatch { width: 16px; height: 16px; margin-right: 19px; }
</style>
</head>
<body>

<!-- Label template repeated per oil -->
<div class="label label--frankincense" style="--tint: var(--frankincense)">
  <div class="label__field">
    <svg viewBox="0 0 100 100" preserveAspectRatio="none" aria-hidden="true">
      <rect width="100" height="100" fill="var(--tint)"/>
      <polygon points="0,70 64,14 100,70 100,100 0,100" fill="var(--paper)"/>
    </svg>
    <div class="label__oil">FRANKINCENSE</div>
    <div class="label__brand"><span class="label__brand-dot"></span><span class="label__brand-name">SOLENNA</span></div>
  </div>
  <div class="label__caution">CAUTION: EYE AND SKIN IRRITANT.<br>Avoid contact with eyes and skin.<br>Wash hands after handling.<br>If eye contact occurs, flush with water for 15 minutes.<br>Not intended for topical or internal use.<br>Contains Essential Oils.<br>KEEP OUT OF REACH OF CHILDREN.</div>
  <div class="label__facts">Ingredients: 100% pure essential oil, GC tested.<br>0.33 fl oz &nbsp;I&nbsp; 10 ml</div>
</div>

<div class="label label--eucalyptus" style="--tint: var(--eucalyptus)">
  <div class="label__field">
    <svg viewBox="0 0 100 100" preserveAspectRatio="none" aria-hidden="true">
      <rect width="100" height="100" fill="var(--tint)"/>
      <polygon points="0,70 64,14 100,70 100,100 0,100" fill="var(--paper)"/>
    </svg>
    <div class="label__oil">EUCALYPTUS</div>
    <div class="label__brand"><span class="label__brand-dot"></span><span class="label__brand-name">SOLENNA</span></div>
  </div>
  <div class="label__caution">CAUTION: EYE AND SKIN IRRITANT.<br>Avoid contact with eyes and skin.<br>Wash hands after handling.<br>If eye contact occurs, flush with water for 15 minutes.<br>Not intended for topical or internal use.<br>Contains Essential Oils.<br>KEEP OUT OF REACH OF CHILDREN.</div>
  <div class="label__facts">Ingredients: 100% pure essential oil, GC tested.<br>0.33 fl oz &nbsp;I&nbsp; 10 ml</div>
</div>

<div class="label label--lavender" style="--tint: var(--lavender)">
  <div class="label__field">
    <svg viewBox="0 0 100 100" preserveAspectRatio="none" aria-hidden="true">
      <rect width="100" height="100" fill="var(--tint)"/>
      <polygon points="0,70 64,14 100,70 100,100 0,100" fill="var(--paper)"/>
    </svg>
    <div class="label__oil">LAVENDER</div>
    <div class="label__brand"><span class="label__brand-dot"></span><span class="label__brand-name">SOLENNA</span></div>
  </div>
  <div class="label__caution">CAUTION: EYE AND SKIN IRRITANT.<br>Avoid contact with eyes and skin.<br>Wash hands after handling.<br>If eye contact occurs, flush with water for 15 minutes.<br>Not intended for topical or internal use.<br>Contains Essential Oils.<br>KEEP OUT OF REACH OF CHILDREN.</div>
  <div class="label__facts">Ingredients: 100% pure essential oil, GC tested.<br>0.33 fl oz &nbsp;I&nbsp; 10 ml</div>
</div>

<div class="label label--peppermint" style="--tint: var(--peppermint)">
  <div class="label__field">
    <svg viewBox="0 0 100 100" preserveAspectRatio="none" aria-hidden="true">
      <rect width="100" height="100" fill="var(--tint)"/>
      <polygon points="0,70 64,14 100,70 100,100 0,100" fill="var(--paper)"/>
    </svg>
    <div class="label__oil">PEPPERMINT</div>
    <div class="label__brand"><span class="label__brand-dot"></span><span class="label__brand-name">SOLENNA</span></div>
  </div>
  <div class="label__caution">CAUTION: EYE AND SKIN IRRITANT.<br>Avoid contact with eyes and skin.<br>Wash hands after handling.<br>If eye contact occurs, flush with water for 15 minutes.<br>Not intended for topical or internal use.<br>Contains Essential Oils.<br>KEEP OUT OF REACH OF CHILDREN.</div>
  <div class="label__facts">Ingredients: 100% pure essential oil, GC tested.<br>0.33 fl oz &nbsp;I&nbsp; 10 ml</div>
</div>

<div class="label label--lemon" style="--tint: var(--lemon)">
  <div class="label__field">
    <svg viewBox="0 0 100 100" preserveAspectRatio="none" aria-hidden="true">
      <rect width="100" height="100" fill="var(--tint)"/>
      <polygon points="0,70 64,14 100,70 100,100 0,100" fill="var(--paper)"/>
    </svg>
    <div class="label__oil">LEMON</div>
    <div class="label__brand"><span class="label__brand-dot"></span><span class="label__brand-name">SOLENNA</span></div>
  </div>
  <div class="label__caution">CAUTION: EYE AND SKIN IRRITANT.<br>Avoid contact with eyes and skin.<br>Wash hands after handling.<br>If eye contact occurs, flush with water for 15 minutes.<br>Not intended for topical or internal use.<br>Contains Essential Oils.<br>KEEP OUT OF REACH OF CHILDREN.</div>
  <div class="label__facts">Ingredients: 100% pure essential oil, GC tested.<br>0.33 fl oz &nbsp;I&nbsp; 10 ml</div>
</div>

<div class="label label--orange" style="--tint: var(--orange)">
  <div class="label__field">
    <svg viewBox="0 0 100 100" preserveAspectRatio="none" aria-hidden="true">
      <rect width="100" height="100" fill="var(--tint)"/>
      <polygon points="0,70 64,14 100,70 100,100 0,100" fill="var(--paper)"/>
    </svg>
    <div class="label__oil">ORANGE</div>
    <div class="label__brand"><span class="label__brand-dot"></span><span class="label__brand-name">SOLENNA</span></div>
  </div>
  <div class="label__caution">CAUTION: EYE AND SKIN IRRITANT.<br>Avoid contact with eyes and skin.<br>Wash hands after handling.<br>If eye contact occurs, flush with water for 15 minutes.<br>Not intended for topical or internal use.<br>Contains Essential Oils.<br>KEEP OUT OF REACH OF CHILDREN.</div>
  <div class="label__facts">Ingredients: 100% pure essential oil, GC tested.<br>0.33 fl oz &nbsp;I&nbsp; 10 ml</div>
</div>

<ul class="palette">
  <li class="palette__item"><span class="palette__swatch" style="background: var(--lavender)"></span>LAVENDER</li>
  <li class="palette__item"><span class="palette__swatch" style="background: var(--cedarwood)"></span>CEDARWOOD</li>
  <li class="palette__item"><span class="palette__swatch" style="background: var(--eucalyptus)"></span>EUCALYPTUS</li>
  <li class="palette__item"><span class="palette__swatch" style="background: var(--frankincense)"></span>FRANKINCENSE</li>
  <li class="palette__item"><span class="palette__swatch" style="background: var(--lemon)"></span>LEMON</li>
  <li class="palette__item"><span class="palette__swatch" style="background: var(--orange)"></span>ORANGE</li>
  <li class="palette__item"><span class="palette__swatch" style="background: var(--peppermint)"></span>PEPPERMINT</li>
  <li class="palette__item"><span class="palette__swatch" style="background: var(--rosemary)"></span>ROSEMARY</li>
  <li class="palette__item"><span class="palette__swatch" style="background: var(--teatree)"></span>TEA TREE</li>
</ul>

</body>
</html>
```